Crestline Plaque & Medal Unique Business Card Design

Recently selected a new logo design and waiting to recieve print files. I've attached image for your review. We are a trophies and awards company that provides engraving on trophies, plaques, name plates, name tags, desk sets, medals, acrylics, and signage.

We are located in Monroe, Louisiana and provide this service with computerized & laser engraving equipment.

Target Market(s)

Corporate, Sport, Church, and Special Events

Industry/Entity Type

Business

Contact Information for Business Card

I'd like to see the following list on the card: Trophies, Plaques, Name Plates, Name Tags, Desk Sets, Medals, Certificates... this is accomplished with Computerized & Laser Engraving

Colors
0555a3
ec1f27
ffffff

Requirements
Must have
• I like either single or double sided. If a design can be created with a frosted card stock I'd consider single. Must be Red, White, and Blue. Dwight Palmer - Owner, 412 W 8th Ave, Monroe, La 71208 office 318-555-0148 fax 318-555-0163 email: info@crestlineplaquemedal.example, and website: www.crestlineplaquemedal.example

```html
<!DOCTYPE html>
<html lang="en">
<head>
<meta charset="utf-8">
<title>Crestline Plaque &amp; Medal – Business Card</title>
<link rel="stylesheet" href="https://fonts.googleapis.com/css2?family=Arimo:wght@400;700&family=Parisienne&display=swap">
<style>
  :root {
    --brand-blue: #0555a3;
    --brand-red: #ec1f27;
    --navy-text: #1f2f66;
    --script-red: #b4191f;
    --band-blue: #2c6c9c;
    --band-red: #c0141c;
    --band-edge: #d8d8dc;
    --frost-light: #f4f5f7;
    --frost-mid: #e3e6ea;
    --page-bg: #d9d6d1;
    --band-text: #e9e3e0;
    --services-text: #3d4670;
  }
  * { margin: 0; padding: 0; box-sizing: border-box; }
  html, body {
    width: 1200px; height: 970px; overflow: hidden;
    background: var(--page-bg);
    font-family: "Arimo", Arial, sans-serif;
  }
  .business-card {
    position: absolute; left: 100px; top: 207px;
    width: 1000px; height: 556px;
    background: linear-gradient(135deg, var(--frost-light) 0%, var(--frost-mid) 55%, #eceef1 100%);
    box-shadow: 0 10px 30px rgba(0,0,0,0.18);
    overflow: hidden;
  }
  .centered { position: absolute; left: 0; width: 100%; text-align: center; white-space: nowrap; }
  .company-name {
    top: 70px; font-size: 50px; font-weight: 700;
    color: var(--brand-blue); letter-spacing: 0.5px;
  }
  .company-rule {
    position: absolute; left: 280px; width: 450px; top: 150px;
    height: 3px; background: var(--brand-blue);
  }
  .person-name {
    top: 178px; font-family: "Parisienne", cursive;
    font-size: 50px; color: var(--script-red);
  }
  .person-title { top: 248px; font-size: 23px; color: var(--navy-text); }
  .phone { top: 300px; font-size: 27px; color: var(--navy-text); }
  .address { top: 336px; font-size: 26px; color: var(--navy-text); }
  .services {
    top: 395px; font-size: 25px; line-height: 26px;
    color: var(--services-text);
  }
  .footer-band { position: absolute; left: 0; top: 461px; width: 1000px; height: 95px; }
  .footer-text {
    position: absolute; top: 500px; font-size: 24px;
    color: var(--band-text); white-space: nowrap;
  }
  .footer-email { left: 36px; }
  .footer-web { left: 515px; width: 470px; text-align: center; }
</style>
</head>
<body>
  <main class="business-card">
    <div class="centered company-name">Crestline Plaque &amp; Medal</div>
    <div class="company-rule"></div>

    <div class="centered person-name">Dwight Palmer</div>
    <div class="centered person-title">Owner</div>

    <div class="centered phone">office 318-555-0148 &nbsp; fax 318-555-0163</div>
    <div class="centered address">412 W 8th Ave, Monroe, La 71208</div>

    <div class="centered services">engraving on trophies, plaques, name plates, name tags, desk sets,<br>medals, certificates, by computerized &amp; laser engraving</div>

    <svg class="footer-band" viewBox="0 0 1000 95" aria-hidden="true">
      <rect x="0" y="0" width="1000" height="95" fill="var(--band-blue)"/>
      <polygon points="445,95 500,18 1000,18 1000,95" fill="var(--band-edge)"/>
      <polygon points="456,95 508,24 1000,24 1000,95" fill="var(--band-red)"/>
    </svg>
    <div class="footer-text footer-email">info@crestlineplaquemedal.example</div>
    <div class="footer-text footer-web">www.crestlineplaquemedal.example</div>
  </main>
</body>
</html>
```